Roofing Contractor business card redesign

I want to redesign my business card with a fresh, eye catching concept

Target Market(s)

Residential Roofing Clients, potential employees, and subcontractors.

Industry/Entity Type

Business

Colors

Designer to choose colors to be used in the design.

Requirements
Nice to have
• I just want something that's more pleasing to the eye. You can use a combination of either / or of my logos.

```html
<!DOCTYPE html>
<html lang="en">
<head>
<meta charset="utf-8">
<title>Fairbuild General Contractors – Business Card</title>
<link href="https://fonts.googleapis.com/css2?family=Nunito+Sans:wght@400;700;800;900&display=swap" rel="stylesheet">
<style>
  :root {
    --backdrop: #5e5e5e;
    --card-white: #ffffff;
    --brand-brown: #4a1810;
    --brand-orange: #ee7a1c;
    --orange-light: #f7a55a;
    --orange-deep: #ec7418;
    --ink: #2a1a16;
  }
  * { box-sizing: border-box; margin: 0; padding: 0; }
  html, body {
    width: 1200px; height: 1200px; overflow: hidden;
    background: var(--backdrop);
    font-family: "Nunito Sans", sans-serif;
  }
  .sheet {
    position: relative; width: 1200px; height: 1200px;
    display: flex; flex-direction: column; align-items: center;
    justify-content: center; gap: 72px;
  }
  .card {
    position: relative; width: 900px; height: 504px;
    border-radius: 14px; overflow: hidden;
  }
  /* Front */
  .card-front { background: var(--card-white); }
  .brand-block {
    position: absolute; left: 70px; top: 50px; width: 300px;
    display: flex; flex-direction: column; align-items: center;
  }
  .brand-disc {
    width: 280px; height: 280px; border-radius: 50%;
    background: radial-gradient(circle at 50% 45%, #f2a24a 0%, #c8601e 55%, var(--brand-brown) 56%);
  }
  .brand-name {
    margin-top: 20px; font-weight: 900; color: var(--brand-brown);
    font-size: 50px; line-height: 1; letter-spacing: -1px;
  }
  .brand-tag {
    margin-top: 8px; font-weight: 900; color: var(--brand-brown);
    font-size: 21px; line-height: 1;
  }
  .details {
    position: absolute; left: 424px; top: 52px; color: var(--ink);
  }
  .person-name {
    font-weight: 800; font-size: 40px; color: var(--brand-brown); line-height: 1.1;
  }
  .person-role {
    margin-top: 6px; font-size: 23px; line-height: 1.3; color: var(--brand-orange);
  }
  .rule {
    width: 40px; height: 3px; background: var(--brand-brown); margin: 18px 0 32px;
  }
  .contact-list { list-style: none; }
  .contact-list li {
    display: flex; align-items: center; gap: 10px;
    font-size: 27px; line-height: 35px;
  }
  .contact-list svg { width: 24px; height: 24px; flex: none; }
  .address { margin-top: 14px; font-size: 27px; line-height: 35px; }
  /* Back */
  .card-back {
    background: linear-gradient(160deg, var(--orange-light) 0%, var(--brand-orange) 55%, var(--orange-deep) 100%);
    display: flex; flex-direction: column; align-items: center; justify-content: center;
  }
  .backdrop-art {
    position: absolute; inset: 0;
    background: radial-gradient(ellipse at 35% 25%, rgba(255,210,150,.45), rgba(236,116,24,0) 60%);
  }
  .back-brand {
    position: relative; display: flex; align-items: center; gap: 22px;
  }
  .back-brand .brand-disc { width: 160px; height: 160px; }
  .back-name {
    font-weight: 900; font-size: 100px; line-height: 1;
    color: var(--brand-brown); letter-spacing: -2px;
  }
  .back-tag {
    position: relative; margin-top: 14px;
    font-weight: 900; font-size: 34px; color: var(--brand-brown);
  }
</style>
</head>
<body>
<main class="sheet">
  <section class="card card-front">
    <div class="brand-block">
      <div class="brand-disc" role="img" aria-label="Company emblem area"></div>
      <div class="brand-name">Fairbuild</div>
      <div class="brand-tag">General Contractors, Inc.</div>
    </div>
    <div class="details">
      <h1 class="person-name">Dale Mercer</h1>
      <p class="person-role">Keller Certified Roof Inspector<br>Licensed Property Adjuster</p>
      <div class="rule"></div>
      <ul class="contact-list">
        <li><svg viewBox="0 0 24 24" fill="none" stroke="#ee7a1c" stroke-width="1.6"><rect x="6" y="2" width="12" height="20" rx="2"/><line x1="10" y1="18.5" x2="14" y2="18.5"/></svg>(555) 201-4386</li>
        <li><svg viewBox="0 0 24 24" fill="none" stroke="#ee7a1c" stroke-width="1.6"><path d="M5 3h4l2 5-2.5 1.5a11 11 0 0 0 6 6L16 13l5 2v4a2 2 0 0 1-2 2A17 17 0 0 1 3 5a2 2 0 0 1 2-2z"/></svg>(555) 201-7700</li>
        <li><svg viewBox="0 0 24 24" fill="none" stroke="#ee7a1c" stroke-width="1.6"><rect x="3" y="5" width="18" height="14"/><path d="M3 5l9 8 9-8M3 19l7-6M21 19l-7-6"/></svg>dale@fairbuildtx.com</li>
        <li><svg viewBox="0 0 24 24" fill="none" stroke="#ee7a1c" stroke-width="1.6"><path d="M3 11l9-8 9 8M5 9.5V21h14V9.5"/><rect x="10" y="14" width="4" height="7"/></svg>www.fairbuildgc.com</li>
      </ul>
      <p class="address">4810 Cedar Ridge Road Suite, 110<br>Plano, TX 75093</p>
    </div>
  </section>

  <section class="card card-back">
    <div class="backdrop-art" role="img" aria-label="Faint house roofline backdrop"></div>
    <div class="back-brand">
      <span class="back-name">Fairbuild</span>
      <div class="brand-disc" role="img" aria-label="Company emblem area"></div>
    </div>
    <p class="back-tag">General Contractors, Inc.</p>
  </section>
</main>
</body>
</html>
```